Business Card Design

We need a design for business cards for our company. We have a logo. We teach EMT's and we are based out of Virginia. The information that will need to add would be, name, title, phone number, email, address. On the back of the business card would be "We help you, help others"

Target Market(s)

People that want to become EMT's

Colors

Designer to choose colors to be used in the design.

Requirements
Must have
• company logo

```html
<!DOCTYPE html>
<html lang="en">
<head>
<meta charset="utf-8">
<title>Medrise Training Co – Business Card</title>
<link href="https://fonts.googleapis.com/css2?family=Montserrat:wght@500;600&family=Roboto:wght@400&display=swap" rel="stylesheet">
<style>
  :root {
    --brand-red: #c01f2f;
    --ink: #2b2b2b;
    --grey: #9a9b9e;
    --paper: #ffffff;
    --backdrop: #eceae6;
  }
  * { box-sizing: border-box; margin: 0; padding: 0; }
  html, body { width: 1200px; height: 900px; overflow: hidden; }
  body {
    background: var(--backdrop);
    position: relative;
    font-family: "Roboto", Arial, sans-serif;
  }
  .card {
    position: absolute;
    width: 600px;
    height: 340px;
    border-radius: 4px;
    box-shadow: 0 10px 28px rgba(0,0,0,0.18);
    overflow: hidden;
  }
  .card-front {
    left: 90px; top: 120px;
    background: var(--brand-red);
    display: flex; align-items: center; justify-content: center;
  }
  .card-back {
    left: 510px; top: 440px;
    background: var(--paper);
  }
  .wordmark {
    display: flex; align-items: center; gap: 10px;
    font-family: "Montserrat", Arial, sans-serif;
    font-weight: 600;
    letter-spacing: 1px;
    white-space: nowrap;
  }
  .wordmark-dot {
    width: 16px; height: 16px; border-radius: 50%; flex: none;
  }
  .card-front .wordmark { color: var(--paper); font-size: 34px; }
  .card-front .wordmark-dot { background: var(--paper); }
  .card-back .wordmark {
    position: absolute; right: 30px; top: 64px;
    color: var(--brand-red); font-size: 20px;
  }
  .card-back .wordmark-dot { background: var(--brand-red); width: 11px; height: 11px; }
  .wave { position: absolute; inset: 0; }
  .holder { position: absolute; left: 40px; top: 40px; }
  .holder-name {
    font-family: "Montserrat", Arial, sans-serif;
    font-weight: 600; font-size: 20px;
    color: var(--brand-red); text-transform: uppercase;
  }
  .holder-title { font-size: 15px; color: var(--ink); margin-top: 2px; }
  .contact {
    position: absolute; left: 40px; top: 162px;
    font-size: 17px; color: var(--ink); line-height: 1.3;
  }
  .contact-line { display: flex; align-items: center; gap: 6px; }
  .contact-icon { width: 18px; height: 14px; flex: none; }
  .contact-address { margin-top: 14px; }
  .tagline {
    position: absolute; right: 28px; bottom: 58px;
    color: var(--paper); font-size: 13px; letter-spacing: 1px;
    text-transform: uppercase;
  }
</style>
</head>
<body>
  <section class="card card-front">
    <div class="wordmark"><span class="wordmark-dot"></span>MEDRISE TRAINING CO</div>
  </section>

  <section class="card card-back">
    <svg class="wave" viewBox="0 0 600 340" preserveAspectRatio="none" aria-hidden="true">
      <path d="M0 300 C160 330 360 250 470 170 C520 135 560 120 600 112 L600 340 L0 340 Z" fill="var(--brand-red)"/>
      <path d="M0 292 C150 318 330 250 440 175 C480 150 500 140 520 134 C480 152 430 200 330 250 C220 300 100 318 0 306 Z" fill="var(--grey)"/>
    </svg>

    <div class="holder">
      <p class="holder-name">Daniel Harper</p>
      <p class="holder-title">Managing Director</p>
    </div>

    <div class="wordmark"><span class="wordmark-dot"></span>MEDRISE TRAINING CO</div>

    <div class="contact">
      <p class="contact-line">
        <svg class="contact-icon" viewBox="0 0 18 14" aria-hidden="true"><path d="M1 5 C4 0 14 0 17 5 L14 6 L12 3.5 L6 3.5 L4 6 Z M4 7 L14 7 L16 13 L2 13 Z" fill="var(--brand-red)"/></svg>
        044-987 654 321
      </p>
      <p class="contact-line">
        <svg class="contact-icon" viewBox="0 0 18 14" aria-hidden="true"><rect x="1" y="1" width="16" height="12" fill="var(--brand-red)"/><path d="M1 1 L9 8 L17 1" fill="none" stroke="#fff" stroke-width="1.4"/></svg>
        hello@medrise.com
      </p>
      <p class="contact-address">421, Address line goes here<br>45452,Country Name</p>
    </div>

    <p class="tagline">We help you, help others</p>
  </section>
</body>
</html>
```